We need UI/UX design for a public, informational website for The Copper Lantern.
The pages, structure, and content scope are already defined. Designers are required to work only on the UI/UX layout of these existing pages, focusing on clarity, hierarchy, spacing, and usability. Do not add, remove, rename, or reinterpret pages or content.
The website is strictly informational only. It must not include accounts, onboarding, payments, custody, escrow administration, marketplaces, dashboards, or any transactional functionality.
Scope of work
Apply UI/UX design to the predefined website pages
Design layout for text, images, notices, and sections
Ensure consistent components and layout patterns across page types
Optimize layouts for long form, compliance focused content
Content writing, page creation, and branding changes are out of scope.
Structure reference
The complete page list, hierarchy, and content definitions are provided in the technical documentation and must be treated as the primary source of truth.
A Figma link is provided only as a light visual reference for page existence and structure:
https://meadow-knot-48203956.plumsite.example/
Designers must rely on the documentation for in depth and authoritative reference.
Brand guidelines
The Copper Lantern has existing brand guidelines and official logos, including light and dark versions. These assets will be provided and must be followed exactly. Designers must not redesign, alter, or reinterpret the brand identity.
Look and feel direction
The desired visual direction is inspired by:
https://ledgerwaltz.example/
This reference is provided only to indicate:
Institutional and enterprise tone
Clean, modern typography
Strong hierarchy and generous whitespace
Editorial, content first layouts
Do not copy branding, layouts, components, or assets from the reference site.
Hero section direction
The hero section should follow a similar structural approach to the hero used on https://ledgerwaltz.example/
, meaning:
Strong editorial framing
Clear headline hierarchy
Calm, institutional first impression
However, the background video must be Abu Dhabi focused, not generic or global. The video should visually reflect:
Abu Dhabi skyline or architectural language
Institutional, sovereign, long term infrastructure tone
Clean, slow, cinematic motion
No promotional, marketing, or lifestyle visuals
The hero must remain informational, restrained, and credible. No hype. No calls to invest. No implied participation.
Constraints
One global primary CTA only: “Continue to Halvemark” (external)
All other interactions must be informational
No visuals or language implying offers, investment, eligibility, or participation
Clear separation between informational content and any external operational platforms
Deliverables
High fidelity UI/UX designs created in Figma, covering:
Desktop layouts
Tablet layouts where relevant
Mobile layouts
Complete Figma file(s) including:
All designed pages defined in the technical documentation
A reusable component library (headers, footers, cards, notice panels, forms, CTAs, typography styles, spacing system)
Clearly defined layout grids, spacing rules, and text styles
Proper use of components and variants, not detached frames
Designs prepared for developer handoff, including:
Clear layer naming and structure
Auto layout where appropriate
Consistent use of styles and components
Responsive behavior demonstrated within Figma
Notes or annotations only where necessary for clarity
No prototypes, interactions, or motion design beyond basic layout states, unless explicitly requested. The focus is static UI/UX clarity, not animation.
A detailed technical specification document and official brand assets will be provided.
Any designs delivered outside Figma, that alter structure or content, or that ignore the defined constraints, boundaries, or tone will be rejected.

```html
<!DOCTYPE html>
<html lang="en">
<head>
<meta charset="utf-8">
<title>The Copper Lantern</title>
<link href="https://fonts.googleapis.com/css2?family=Space+Grotesk:wght@400;500;600;700&family=Poppins:ital,wght@0,400;0,500;1,400&display=swap" rel="stylesheet">
<style>
:root{
  --ink:#111111;
  --text:#2b2b2b;
  --muted:#444;
  --band:#eeeeee;
  --white:#ffffff;
  --accent:#2ad4f5;
  --footer:#1d1d1d;
  --footer-text:#d8d8d8;
  --footer-muted:#8a8a8a;
  --ring:#e3e3e3;
}
*{box-sizing:border-box;margin:0;padding:0}
html,body{width:1200px;height:4598px;overflow:hidden}
body{position:relative;background:var(--white);font-family:"Poppins",sans-serif;color:var(--text)}
.abs{position:absolute}
h1,h2,h3,.nav,.btn{font-family:"Space Grotesk",sans-serif}
.btn{position:absolute;display:flex;align-items:center;justify-content:center;font-size:15px;font-weight:600;letter-spacing:.3px;text-transform:uppercase;text-decoration:none}
.btn-dark{background:var(--ink);color:var(--white)}
.btn-accent{background:var(--accent);color:var(--white)}
/* hero */
.hero{left:0;top:0;width:1200px;height:721px;background:linear-gradient(125deg,#b4552a 0%,#7e4a3a 22%,#3a4250 48%,#2c3a44 70%,#24333a 100%)}
.hero-shade{inset:0;background:linear-gradient(90deg,rgba(0,0,0,.35),rgba(0,0,0,.05) 70%)}
.logo{display:flex;align-items:center;gap:10px;color:var(--white);font-family:"Space Grotesk",sans-serif;font-weight:500;font-size:20px;letter-spacing:.5px;text-transform:uppercase}
.logo-dot{width:16px;height:16px;border-radius:50%;border:2px solid var(--accent)}
.nav{left:358px;top:72px;display:flex;gap:48px;font-size:13px;font-weight:600;color:var(--white);letter-spacing:.3px}
.nav .active{text-decoration:underline;text-underline-offset:5px}
.hero h1{left:73px;top:292px;font-size:66px;font-weight:600;color:var(--white);letter-spacing:.5px}
.hero-lede{left:77px;top:378px;width:640px;font-size:17.5px;line-height:24px;color:var(--white);font-family:"Space Grotesk",sans-serif;font-weight:500}
/* feature sections */
.band{left:0;width:1200px;background:var(--band)}
.photo{border-radius:10px}
.photo-round{border-radius:50%;border:5px solid var(--ring)}
.feature h2{font-size:35px;font-weight:500;color:var(--ink);line-height:40px;letter-spacing:.3px}
.feature p{font-size:14.5px;line-height:25.5px;color:var(--muted);margin-top:14px}
.feature p + p{margin-top:14px}
/* layers */
.layers-title{left:0;width:1200px;top:2306px;text-align:center;font-size:35px;font-weight:500;color:var(--ink)}
.layers-sub{left:0;width:1200px;top:2370px;text-align:center;font-size:14.5px;color:var(--muted)}
.layer{width:322px;height:322px;border-radius:50%;background:var(--white);border:5px solid var(--ring);text-align:center;padding:54px 38px 0}
.layer-num{width:50px;height:50px;border-radius:50%;background:var(--ink);color:var(--white);margin:0 auto;display:flex;align-items:center;justify-content:center;font-family:"Space Grotesk",sans-serif;font-size:24px;font-weight:600}
.layer h3{font-size:25px;font-weight:500;color:var(--ink);margin-top:20px}
.layer p{font-size:14px;line-height:24px;color:var(--muted);margin-top:6px}
.layers-note{left:100px;width:1000px;top:2777px;text-align:center;font-size:14.5px;line-height:25px;font-style:italic;color:var(--ink)}
/* contact */
.contact{top:3899px;height:348px;background:linear-gradient(180deg,#ececec,#f4f4f4)}
.contact h2{position:absolute;left:0;width:1200px;top:64px;text-align:center;font-size:35px;font-weight:500;color:var(--ink)}
.contact p{position:absolute;left:160px;width:880px;top:120px;text-align:center;font-size:14.5px;line-height:26px;color:var(--muted)}
.contact .btn{text-transform:none;font-size:16px;font-weight:500}
/* footer */
.footer{left:0;top:4247px;width:1200px;height:351px;background:var(--footer);color:var(--footer-text)}
.footer h4{font-family:"Space Grotesk",sans-serif;font-size:19px;font-weight:600;color:var(--white);letter-spacing:.3px}
.footer-links{display:grid;grid-template-columns:153px 120px;row-gap:11px;margin-top:14px;font-size:14.5px}
.footer-info{margin-top:14px;font-size:14.5px;line-height:31px}
.social{display:flex;gap:18px;margin-top:12px}
.social span{width:20px;height:20px;border-radius:50%;background:var(--footer-text)}
.copy{font-size:12px;line-height:23px;color:var(--footer-text)}
.notice{left:75px;top:4518px;width:1050px;font-size:11.5px;line-height:25px;color:var(--footer-muted)}
.notice strong{font-weight:500;color:#a9a9a9;display:block}
</style>
</head>
<body>

<!-- Hero -->
<section class="abs hero">
  <div class="abs hero-shade" role="img" aria-label="Abu Dhabi skyline at sunset seen over the waterfront"></div>
  <div class="abs logo" style="left:75px;top:70px"><span class="logo-dot"></span>The Copper Lantern</div>
  <nav class="abs nav">
    <span class="active">HOME</span><span>FRAMEWORK</span><span>PROJECTS</span><span>HALVEMARK</span><span>INSIGHTS</span><span>COMPANY</span><span>CONTACT</span>
  </nav>
  <h1 class="abs">THE COPPER LANTERN</h1>
  <p class="abs hero-lede">Duis mollis, est non commodo luctus, nisi erat porttitor ligula, eget lacinia odio sem nec elit. Morbi leo risus, porta ac consectetur ac, vestibu lum at eros. Nulla vitae elit libero.</p>
  <a class="btn btn-dark" style="left:73px;top:476px;width:226px;height:53px">Continue to Halvemark</a>
  <a class="btn btn-accent" style="left:310px;top:476px;width:224px;height:53px">Learn the Framework</a>
</section>

<!-- About -->
<div class="abs photo" style="left:75px;top:790px;width:512px;height:386px;background:linear-gradient(160deg,#9fb6c9,#4c6a74 45%,#2f5a4f 70%,#5a6a72)" role="img" aria-label="Aerial view of marina towers and waterway"></div>
<section class="abs feature" style="left:616px;top:802px;width:510px">
  <h2>The Copper Lantern</h2>
  <p>The Copper Lantern is a governance and project origination group. Its purpose is to define structural standards and oversight principles for complex initiatives that may involve multiple parties, staged execution, and long-term accountability. This website publishes those standards and explains how responsibilities are separated across governance, operations, and project-level execution.</p>
  <p>This site is informational. It does not provide onboarding, account access, eligibility checks, custody of funds, escrow administration, or transaction execution. Where operational workflows exist, they are provided through a separate operating platform under separate terms and policies.</p>
</section>

<!-- Governance -->
<div class="abs band" style="top:1304px;height:375px"></div>
<section class="abs feature" style="left:75px;top:1354px;width:540px">
  <h2>Governance and Project<br>Origination</h2>
  <p>Governance in this context refers to the standards that determine how projects are structured and how oversight is described. Origination refers to the initial design and definition of an initiative, including role separation, reporting expectations, and boundary setting before execution begins. The Copper Lantern focuses on these governance-level elements rather than on operating day-to-day workflows.</p>
</section>
<div class="abs photo-round" style="left:648px;top:1253px;width:477px;height:477px;background:linear-gradient(170deg,#5a6a9a,#7a5a6a 40%,#b08040 70%,#3a3a50)" role="img" aria-label="Downtown skyscrapers lit at dusk"></div>

<!-- Role separation -->
<div class="abs photo" style="left:75px;top:1790px;width:512px;height:386px;background:linear-gradient(180deg,#2f5c9c,#4c7ab0 40%,#b5894e 70%,#2a3a55)" role="img" aria-label="City towers reflected on water at blue hour"></div>
<section class="abs feature" style="left:616px;top:1800px;width:510px">
  <h2>Clear Role Separation</h2>
  <p>The ecosystem is designed around clear separation of responsibilities. Governance activities belong at the framework layer. Operational workflows, where available, belong on a separate operating platform designed for process execution and recordkeeping. Assets and project execution, where applicable, belong at the project level through ring-fenced structures created for specific initiatives. This separation is intended to reduce ambiguity and help stakeholders understand who is responsible for what.</p>
</section>
<a class="btn btn-dark" style="left:616px;top:2107px;width:222px;height:53px">Continue to Halvemark</a>

<!-- Ecosystem layers -->
<div class="abs band" style="top:2259px;height:375px"></div>
<h2 class="abs layers-title">How the Ecosystem Works</h2>
<p class="abs layers-sub">At a high level, the ecosystem can be understood as three layers</p>
<div class="abs layer" style="left:78px;top:2425px"><div class="layer-num">1</div><h3>Governance</h3><p>Defines standards, explains role boundaries, and publishes framework information.</p></div>
<div class="abs layer" style="left:439px;top:2425px"><div class="layer-num">2</div><h3>Operations</h3><p>Manages workflow processes such as documentation steps and record-anchored audit events through a separate platform.</p></div>
<div class="abs layer" style="left:803px;top:2425px"><div class="layer-num">3</div><h3>Project Execution</h3><p>Occurs at the project level through dedicated structures that hold responsibilities and assets where applicable.</p></div>
<p class="abs layers-note">This website focuses on the governance layer and provides links to learn about structural concepts such as role separation, escrow and milestone framing, and recordkeeping terminology.</p>

<!-- Escrow -->
<div class="abs band" style="top:2952px;height:375px"></div>
<section class="abs feature" style="left:75px;top:3012px;width:540px">
  <h2>Independent Escrow and<br>Milestone Oversight</h2>
  <p>Some initiatives use independent escrow arrangements to coordinate staged releases linked to milestone completion. Escrow can support execution discipline by requiring defined evidence before releases occur. Escrow does not guarantee outcomes, timelines, or success, and it is not administered by this website operator. This site describes the concept for clarity and transparency.</p>
</section>
<div class="abs photo-round" style="left:648px;top:2902px;width:477px;height:477px;background:linear-gradient(180deg,#7fa8c4,#c9b48a 35%,#5a7a95 60%,#2e4a68)" role="img" aria-label="Skyline of glass towers in warm daylight"></div>

<!-- Operational workflows -->
<div class="abs photo" style="left:75px;top:3436px;width:512px;height:386px;background:linear-gradient(180deg,#3a4a70,#6a6a80 40%,#8a7a6a 65%,#2a2e30)" role="img" aria-label="Low-rise residences at dusk with skyline behind"></div>
<section class="abs feature" style="left:616px;top:3476px;width:510px">
  <h2>Where Operational<br>Workflows Happen</h2>
  <p>Operational workflows, including any onboarding or workflow participation where permitted, occur on a separate operating platform under separate terms and policies. If you need operational access, use the Halvemark page on this site to navigate externally. This website does not host those workflows.</p>
</section>
<a class="btn btn-accent" style="left:616px;top:3724px;width:224px;height:53px">Learn the Framework</a>

<!-- Contact -->
<section class="abs band contact">
  <h2>Contact and Inquiries</h2>
  <p>If you have questions about governance framework concepts, role boundaries, or information published on this website, you can contact the team using the Contact page. Do not submit sensitive personal data through public forms.</p>
  <a class="btn btn-dark" style="left:489px;top:227px;width:222px;height:53px">Contact the Team</a>
</section>

<!-- Footer -->
<footer class="abs footer">
  <div class="abs logo" style="left:75px;top:98px"><span class="logo-dot"></span>The Copper Lantern</div>
  <p class="abs copy" style="left:75px;top:180px">© Copyright © 2026 Company Name.<br>All Right Reserved</p>
  <div class="abs" style="left:434px;top:50px">
    <h4>QUICK LINKS</h4>
    <div class="footer-links"><span>Framework</span><span>Company</span><span>Projects</span><span>Contact</span><span>Halvemark</span><span>Legal</span><span>Insights</span><span>Glossary</span></div>
  </div>
  <div class="abs" style="left:795px;top:50px">
    <h4>CONTACT INFO</h4>
    <div class="footer-info">48 Harrow Quay Suite 210,<br>Portland 97201, United States<br>+1-555-014-2290<br>hello@copperlantern.example</div>
    <div class="social"><span></span><span></span><span></span><span></span><span></span></div>
  </div>
</footer>
<p class="abs notice"><strong>Informational notice:</strong>This website is provided for general informational purposes only. Nothing on this site is an offer, solicitation, or professional advice.</p>

</body>
</html>
```